Commercial Loan Originator Business Card (CHANGE COLORS SCHEME)

CHANGE COLOR SCHEME - SAME DESIGN

Name Marlene Agate
Title Commercial Loan Originator
Office (800) 417-2906 x68
Direct (240) 615-2043
Email freshgreens4life@quillbox.example

Name Dale Morrow
Office (800) 417-2906 x70
Direct (410) 392-5184
Email d.morthehomeguy@quillbox.example

Name Leonard Vasko
Office (800) 417-2906 x71
Direct (215) 463-0712
Email l.vasko41@quillbox.example

Name Gwen Halsey
Office (800) 417-2906 x
Direct (202) 548-1370
Email ghalsey63@quillbox.example

Name Mirna Ashby
Office (800) 417-2906 x72
Direct (240) 871-4526
Email tristatehomelending@quillbox.example

```html
<!DOCTYPE html>
<html lang="en">
<head>
<meta charset="utf-8">
<title>Leonard Vasko – Business Card</title>
<link href="https://fonts.googleapis.com/css2?family=Playfair+Display:wght@800&family=Marcellus&family=Poppins:wght@400&display=swap" rel="stylesheet">
<style>
  :root {
    --backdrop: #808080;
    --card: #ffffff;
    --ink: #13263a;
    --band: #0f2e47;
    --surname: #2f8a8f;
    --portrait-a: #2a3a66;
    --portrait-b: #1b2444;
  }
  html, body {
    margin: 0;
    width: 1003px;
    height: 1200px;
    overflow: hidden;
    background: var(--backdrop);
  }
  .card {
    position: absolute;
    left: 150px;
    width: 702px;
    height: 401px;
    background: var(--card);
    box-shadow: 0 6px 22px rgba(0,0,0,0.35);
    display: block;
  }
  .card--front { top: 144px; }
  .card--back { top: 654px; }
  .band { fill: var(--band); }
  .given-name { font-family: "Playfair Display", serif; font-weight: 800; font-size: 128px; fill: var(--ink); }
  .surname { font-family: "Playfair Display", serif; font-weight: 800; font-size: 128px; fill: var(--surname); }
  .job-title { font-family: "Marcellus", serif; font-size: 40px; fill: var(--ink); }
  .job-title--back { font-size: 34px; }
  .contact { font-family: "Poppins", sans-serif; font-size: 25px; fill: var(--ink); }
  .divider { stroke: var(--ink); }
  .icon-dot { fill: var(--ink); }
  .icon-glyph { fill: none; stroke: #fff; stroke-width: 1.6; }
</style>
</head>
<body>

<svg class="card card--front" viewBox="0 0 1050 600" aria-label="Business card front">
  <polygon class="band" points="0,0 365,0 0,197"/>
  <polygon class="band" points="1050,400 1050,600 680,600"/>
  <text class="given-name" x="525" y="262" text-anchor="middle">LEONARD</text>
  <text class="surname" x="525" y="372" text-anchor="middle">VASKO</text>
  <text class="job-title" x="525" y="435" text-anchor="middle">COMMERCIAL LOAN ORIGINATOR</text>
</svg>

<svg class="card card--back" viewBox="0 0 1050 600" aria-label="Business card back">
  <defs>
    <linearGradient id="portraitTone" x1="0" y1="0" x2="0" y2="1">
      <stop offset="0" stop-color="var(--portrait-a)"/>
      <stop offset="1" stop-color="var(--portrait-b)"/>
    </linearGradient>
  </defs>
  <polygon class="band" points="295,600 1050,190 1050,520 915,600"/>
  <path d="M795 110 Q795 45 872 45 Q950 45 950 110 L950 250 L1050 290 L1050 600 L680 600 L705 300 L795 255 Z" fill="url(#portraitTone)" role="img" aria-label="Portrait photo of the loan originator in a navy suit"/>

  <text class="given-name" x="58" y="172">LEONARD</text>
  <text class="surname" x="58" y="283">VASKO</text>
  <text class="job-title job-title--back" x="58" y="342">COMMERCIAL LOAN ORIGINATOR</text>
  <line class="divider" x1="60" y1="381" x2="246" y2="381" stroke-width="4" stroke-dasharray="0.1 9" stroke-linecap="round"/>

  <g class="contact-row">
    <circle class="icon-dot" cx="67" cy="434" r="10"/>
    <rect class="icon-glyph" x="63" y="428" width="8" height="12"/>
    <text class="contact" x="84" y="443">(800) 417-2906 x71</text>
  </g>
  <g class="contact-row">
    <circle class="icon-dot" cx="67" cy="471" r="10"/>
    <path class="icon-glyph" d="M63 466 q0 8 8 10"/>
    <text class="contact" x="84" y="480">(215) 463-0712</text>
  </g>
  <g class="contact-row">
    <circle class="icon-dot" cx="67" cy="510" r="10"/>
    <rect class="icon-glyph" x="62" y="506" width="10" height="8"/>
    <path class="icon-glyph" d="M62 506 l5 4 l5 -4"/>
    <text class="contact" x="84" y="518">l.vasko41@quillbox.example</text>
  </g>
</svg>

</body>
</html>
```